Heron Loan Partners Business Card

We need a business card design for our mortgage servicing company. In addition to servicing the loans of homeowners, we help homeowners with purchasing their homes and any mortgage refinancing. We would like to see designs that use the colors in the logo attached below (gold-ish yellow and navy blue), and any other design you deem fit! The design should communicate a simpler life with smart mortgages provided by Heron.

```html
<!DOCTYPE html>
<html lang="en">
<head>
<meta charset="utf-8">
<title>Heron Loan Partners Business Card</title>
<link href="https://fonts.googleapis.com/css2?family=Montserrat:wght@600;700&family=Lato:wght@400;700&display=swap" rel="stylesheet">
<style>
  :root {
    --navy: #2e2a63;
    --gold: #e2b33c;
    --white: #ffffff;
    --ink: #2b2b35;
    --backdrop: #e9e9ec;
  }
  * { box-sizing: border-box; margin: 0; padding: 0; }
  html, body { width: 1200px; height: 900px; overflow: hidden; }
  body {
    background: var(--backdrop);
    font-family: "Lato", sans-serif;
    position: relative;
  }
  .card {
    position: absolute;
    left: 250px;
    width: 700px;
    height: 400px;
    overflow: hidden;
    box-shadow: 0 6px 18px rgba(0,0,0,0.18);
  }
  .card--front { top: 35px; background: var(--navy); }
  .card--back { top: 465px; background: var(--white); }

  .brand {
    position: absolute;
    display: flex;
    align-items: center;
    gap: 14px;
    font-family: "Montserrat", sans-serif;
    font-weight: 700;
    color: var(--gold);
    white-space: nowrap;
  }
  .brand__dot {
    border-radius: 50%;
    background: var(--gold);
    flex: none;
  }
  .card--front .brand {
    left: 0; right: 0; top: 170px;
    justify-content: center;
    font-size: 44px;
  }
  .card--front .brand__dot { width: 26px; height: 26px; }
  .card--back .brand {
    left: 250px; top: 95px;
    font-size: 28px;
  }
  .card--back .brand__dot { width: 18px; height: 18px; background: var(--navy); }

  .person {
    position: absolute;
    left: 50px;
    top: 244px;
  }
  .person__name {
    font-family: "Montserrat", sans-serif;
    font-weight: 700;
    font-size: 26px;
    color: var(--navy);
    letter-spacing: 0.3px;
    line-height: 1.1;
    white-space: nowrap;
  }
  .person__title {
    font-family: "Lato", sans-serif;
    font-size: 18px;
    color: var(--gold);
    margin-top: 2px;
  }

  .rule {
    position: absolute;
    height: 1.5px;
    background: var(--navy);
  }
  .rule--left { left: 50px; top: 310px; width: 240px; }
  .rule--right { left: 305px; top: 236px; width: 370px; }

  .contact {
    position: absolute;
    list-style: none;
    color: var(--ink);
    white-space: nowrap;
  }
  .contact li {
    display: flex;
    align-items: center;
    gap: 10px;
  }
  .contact svg { width: 14px; height: 14px; flex: none; }
  .contact--phones { left: 52px; top: 320px; font-size: 18px; }
  .contact--phones li { height: 28px; }
  .contact--online { left: 307px; top: 250px; font-size: 14px; }
  .contact--online li { height: 24px; }

  .address {
    position: absolute;
    left: 548px;
    top: 250px;
    font-size: 14px;
    line-height: 24px;
    font-style: normal;
    color: var(--ink);
    white-space: nowrap;
  }
</style>
</head>
<body>

<section class="card card--front" aria-label="Card front">
  <div class="brand">
    <span class="brand__dot"></span>
    <span class="brand__name">Heron Loan Partners</span>
  </div>
</section>

<section class="card card--back" aria-label="Card back">
  <div class="brand">
    <span class="brand__dot"></span>
    <span class="brand__name">Heron Loan Partners</span>
  </div>

  <div class="person">
    <h1 class="person__name">DANIEL BROOKS</h1>
    <p class="person__title">Founder &amp; CEO</p>
  </div>

  <div class="rule rule--left"></div>
  <div class="rule rule--right"></div>

  <ul class="contact contact--phones">
    <li>
      <svg viewBox="0 0 16 16" aria-hidden="true"><path fill="#e2b33c" d="M3.2 1.5l2.3 2.6-1.3 1.6c.9 2 2.6 3.7 4.6 4.6l1.6-1.3 2.6 2.3-1.4 2.2C6.8 13.3 2.7 9.2 1 4.4z"/></svg>
      <span>(555) 214-3870</span>
    </li>
    <li>
      <svg viewBox="0 0 16 16" aria-hidden="true"><rect x="4" y="1" width="8" height="14" rx="1.5" fill="none" stroke="#e2b33c" stroke-width="1.6"/><circle cx="8" cy="12.3" r="0.9" fill="#e2b33c"/></svg>
      <span>(555) 214-3871</span>
    </li>
  </ul>

  <ul class="contact contact--online">
    <li>
      <svg viewBox="0 0 16 16" aria-hidden="true"><rect x="1" y="3" width="14" height="10" fill="#e2b33c"/><path d="M1 3l7 6 7-6" fill="none" stroke="#fff" stroke-width="1.3"/></svg>
      <span>info@heronloanpartners.com</span>
    </li>
    <li>
      <svg viewBox="0 0 16 16" aria-hidden="true"><circle cx="8" cy="8" r="6.5" fill="none" stroke="#e2b33c" stroke-width="1.5"/><path d="M1.5 8h13M8 1.5c-3 3.5-3 9.5 0 13M8 1.5c3 3.5 3 9.5 0 13" fill="none" stroke="#e2b33c" stroke-width="1.1"/></svg>
      <span>www.heronloanpartners.com</span>
    </li>
  </ul>

  <address class="address">
    Your Address, City<br>
    State, Zip Code 1235
  </address>
</section>

</body>
</html>
```